Advertising company unique advertising platform

we need a logo design for a new company based in Australia Melbourne. We develop innovated advertising platform where consumer can use this platform to get regular discount, as business owner they can use this platform for free advertisement. Payment for this advertisement platform only payable every two weeks, when I generate revenue for their business

Industry/Entity Type

Advertising

Contact Information for Business Card

Dale Morven | Co-Founder |Managing Director
Suite 718 240 Wattlebrook Lane Melbourne Vic 3000

ABN 38 614 207 923
Tel: +61 0487 259 318 | Email: dale.morven@plivorantu.com

Font styles to use
Decorative
Script

Requirements
Must have
• Try few different design and some round corner business card
Should not have
• One round corner business card...try 4 different colour background not only black, make sure two side is designed. Be creative so imagine you are giving this to a client make sure has wow factor, if you can also try one design with engrave like all the logo, words look 3d feel
• The word Advertising Platform use attached file font

```html
<!DOCTYPE html>
<html lang="en">
<head>
<meta charset="utf-8">
<title>Plivo Rantu – Business Card</title>
<link rel="stylesheet" href="https://fonts.googleapis.com/css2?family=Open+Sans:wght@400;600;700&display=swap">
<style>
  :root {
    --backdrop: #7a4e33;
    --card-dark: #2b2b2b;
    --ink-dark: #1c1410;
    --ink-light: #f2f2f2;
    --orange-deep: #e0502e;
    --orange-warm: #f0a03c;
    --sun: #f2cd4c;
    --teal: #19e0b0;
    --sky: #6a9fd0;
    --brand: #1fe0b4;
    --brand-dot: #f06a2a;
  }
  * { margin: 0; padding: 0; box-sizing: border-box; }
  html, body { width: 1200px; height: 960px; overflow: hidden; }
  body {
    position: relative;
    background: var(--backdrop);
    font-family: "Open Sans", Arial, sans-serif;
  }
  .card {
    position: absolute;
    width: 602px;
    height: 344px;
    border-radius: 22px;
    overflow: hidden;
    background: var(--card-dark);
    box-shadow: 0 6px 14px rgba(0,0,0,0.45);
  }
  .card--front { left: 313px; top: 113px; }
  .card--back  { left: 311px; top: 472px; width: 600px; }
  .card__art { position: absolute; inset: 0; }
  .contact {
    position: absolute;
    left: 27px;
    top: 24px;
    color: var(--ink-dark);
    font-size: 14.5px;
    line-height: 20px;
  }
  .contact__name { font-weight: 700; font-size: 16px; line-height: 22px; }
  .contact__role { font-size: 16px; line-height: 22px; }
  .contact__company { margin-top: 8px; }
  .contact__address { margin-top: 3px; }
  .contact__lines { margin-top: 8px; }
  .contact__line { display: flex; align-items: center; gap: 8px; font-size: 14px; }
  .contact__line svg { width: 14px; height: 12px; fill: var(--ink-dark); }
  .brand {
    position: absolute;
    display: flex;
    align-items: center;
    gap: 10px;
    color: var(--brand);
    font-weight: 600;
    white-space: nowrap;
  }
  .brand__dot { border-radius: 50%; background: var(--brand-dot); flex: none; }
  .card--front .brand { left: 346px; top: 222px; font-size: 25px; }
  .card--front .brand__dot { width: 26px; height: 26px; }
  .card--back .brand { left: 50%; top: 124px; transform: translateX(-50%); font-size: 42px; gap: 12px; }
  .card--back .brand__dot { width: 42px; height: 42px; }
  .website {
    position: absolute;
    left: 0; right: 0;
    top: 292px;
    text-align: center;
    color: var(--ink-light);
    font-size: 14px;
    letter-spacing: 5px;
  }
</style>
</head>
<body>

<section class="card card--front">
  <svg class="card__art" viewBox="0 0 602 344" aria-hidden="true">
    <defs>
      <radialGradient id="warmGlow" cx="230" cy="170" r="300" gradientUnits="userSpaceOnUse">
        <stop offset="0" stop-color="var(--sun)"/>
        <stop offset="0.45" stop-color="var(--orange-warm)"/>
        <stop offset="1" stop-color="var(--orange-deep)"/>
      </radialGradient>
      <linearGradient id="ribbon" x1="0" y1="0" x2="0" y2="1">
        <stop offset="0" stop-color="var(--sky)"/>
        <stop offset="1" stop-color="var(--teal)"/>
      </linearGradient>
    </defs>
    <path d="M387 0 H412 C360 10 335 80 315 150 C290 240 250 335 160 344 H130 C230 330 255 220 280 130 C300 60 330 0 387 0 Z" fill="url(#ribbon)"/>
    <path d="M0 0 H387 C330 0 300 60 280 130 C255 220 230 330 130 344 H0 Z" fill="url(#warmGlow)"/>
  </svg>

  <div class="contact">
    <div class="contact__name">DALE MORVEN</div>
    <div class="contact__role">CO-FOUNDER</div>
    <div class="contact__role">MANAGING DIRECTOR</div>
    <div class="contact__company">Plivo Rantu<br>ABN 38 614 207 923</div>
    <div class="contact__address">Suite 718 240 Wattlebrook Lane<br>Melbourne Vic 3000</div>
    <div class="contact__lines">
      <div class="contact__line">
        <svg viewBox="0 0 14 12" aria-hidden="true"><path d="M1 4 C1 1 13 1 13 4 L11 5 L10 3 H4 L3 5 Z M3 6 H11 L12 11 H2 Z"/></svg>
        <span>+61 0487 259 318</span>
      </div>
      <div class="contact__line">
        <svg viewBox="0 0 14 12" aria-hidden="true"><path d="M1 2 H13 V10 H1 Z M1 2 L7 7 L13 2" stroke="#f5b040" stroke-width="0.8"/></svg>
        <span>dale.morven@plivorantu.com</span>
      </div>
    </div>
  </div>

  <div class="brand"><span class="brand__dot"></span><span class="brand__name">Stallpoint Hub</span></div>
</section>

<section class="card card--back">
  <div class="brand"><span class="brand__dot"></span><span class="brand__name">Stallpoint Hub</span></div>
  <div class="website">www.plivorantu.com</div>
</section>

</body>
</html>
```